Tolbek cards

I want a simple business card that pops.
Logo on one side.
On side two i want.
"Are you thinking about a new building on your property, or renovating an existing structure? Contact".....
Owners Name: Dale Whitacre
Owners Phone number: 610-555-0187
Address:4076 Copper Ridge RD, Linwood, OH 43021
Committed to Quality, Service, and Integrity

```html
<!DOCTYPE html>
<html lang="en">
<head>
<meta charset="utf-8">
<title>Tolbek Builders – Business Card</title>
<link href="https://fonts.googleapis.com/css2?family=Arimo:ital,wght@0,400;0,700;1,700&display=swap" rel="stylesheet">
<style>
  :root {
    --backdrop: #5b5b5b;
    --card: #ffffff;
    --brown: #5a3e25;
    --brown-deep: #43301d;
    --ink: #1f1f1f;
    --grey-text: #555555;
    --rule: #3b4a5a;
  }
  * { margin: 0; padding: 0; box-sizing: border-box; }
  html, body {
    width: 1200px; height: 1200px; overflow: hidden;
    background: var(--backdrop);
    font-family: "Arimo", Arial, sans-serif;
  }
  .card {
    position: absolute;
    background: var(--card);
    width: 690px; height: 394px;
  }
  .card--contact { left: 266px; top: 158px; }
  .card--brand { left: 260px; top: 651px; width: 692px; height: 395px; }

  .headline {
    position: absolute; left: 0; right: 0; top: 52px;
    text-align: center;
    font-style: italic; font-weight: 700;
    font-size: 18px; line-height: 25px;
    color: var(--brown);
  }
  .owner-name {
    position: absolute; left: 51px; top: 193px;
    font-weight: 700; font-size: 29px; letter-spacing: 0.6px;
    line-height: 34px;
    color: var(--brown);
  }
  .divider {
    position: absolute; left: 318px; top: 187px;
    width: 1px; height: 47px; background: var(--rule);
  }
  .contact-lines {
    position: absolute; left: 334px; top: 190px;
    font-size: 16px; line-height: 23px; color: var(--grey-text);
  }
  .contact-lines .phone { display: flex; align-items: center; gap: 10px; }
  .contact-lines svg { width: 13px; height: 13px; fill: var(--brown); }
  .tagline {
    position: absolute; left: 0; right: 0; top: 337px;
    text-align: center; font-size: 18px; color: var(--ink);
  }

  .wordmark__mark {
    position: absolute; left: 114px; top: 117px;
    width: 118px; height: 118px; background: var(--brown-deep);
  }
  .wordmark__name {
    position: absolute; left: 269px; top: 148px;
    font-weight: 700; color: var(--brown-deep);
    text-transform: uppercase; line-height: 1;
  }
  .wordmark__name .main { display: block; font-size: 74px; letter-spacing: 0.5px; }
  .wordmark__name .sub { display: block; font-size: 25px; letter-spacing: 1.5px; margin-top: 8px; }
</style>
</head>
<body>
  <section class="card card--contact">
    <p class="headline">Are you thinking about a new building on your property,<br>or renovating an existing structure?</p>
    <h1 class="owner-name">DALE WHITACRE</h1>
    <div class="divider"></div>
    <div class="contact-lines">
      <div class="phone">
        <svg viewBox="0 0 24 24" aria-hidden="true"><path d="M6.6 10.8a15.1 15.1 0 0 0 6.6 6.6l2.2-2.2c.3-.3.7-.4 1-.2 1.1.4 2.3.6 3.6.6.6 0 1 .4 1 1V20c0 .6-.4 1-1 1C10.6 21 3 13.4 3 4c0-.6.4-1 1-1h3.5c.6 0 1 .4 1 1 0 1.3.2 2.5.6 3.6.1.3 0 .7-.2 1z"/></svg>
        <span>610-555-0187</span>
      </div>
      <div class="address">4076 Copper Ridge RD, Linwood, OH 43021</div>
    </div>
    <p class="tagline">Committed to Quality, Service, and Integrity</p>
  </section>

  <section class="card card--brand">
    <div class="wordmark__mark"></div>
    <div class="wordmark__name">
      <span class="main">Tolbek</span>
      <span class="sub">Builders LLC</span>
    </div>
  </section>
</body>
</html>
```